Folder Design (inside and out) for a medical technology company

We are a Medical Technology company looking for a professional folder design.
Folder design is for Front, Back, and the flaps inside the folder. We've provided a variety of products at a national level for 20 years, we're targeting a demographic of doctors and are looking to improve out materials.

I attached our logo for reference, please feel free to reach out if you have any questions. Please use the pink and blue logo.

Thank you.

Target Market(s)

Doctors

Industry/Entity Type

Medical, Technology

Requirements
Must have
• Professional design

```html
<!DOCTYPE html>
<html lang="en">
<head>
<meta charset="utf-8">
<title>Veridian Medical – Presentation Folder</title>
<link rel="stylesheet" href="https://fonts.googleapis.com/css2?family=Poppins:wght@300;400;500;600;700;800&display=swap">
<style>
  :root {
    --blue: #6a93cc;
    --blue-deep: #5a82c0;
    --pink: #ec5d8a;
    --ink: #2b2b2b;
    --paper: #ffffff;
    --paper-top: #f5f5f5;
    --paper-bottom: #fbfbfb;
    --pattern-grey: #e4e4e4;
    --watermark: #ececec;
    --stage: #ffffff;
    --badge: #1f7a4a;
  }
  html, body {
    margin: 0;
    padding: 0;
    width: 711px;
    height: 1200px;
    overflow: hidden;
    background: var(--stage);
  }
  .canvas {
    position: relative;
    width: 711px;
    height: 1200px;
  }
  .folder-dieline {
    position: absolute;
    left: 20px;
    top: 264px;
    width: 671px;
    height: 672px;
    filter: drop-shadow(0 4px 10px rgba(0,0,0,0.28));
    font-family: 'Poppins', sans-serif;
  }
  .headline-light { font-weight: 300; fill: var(--blue-deep); }
  .headline-bold { font-weight: 700; fill: var(--pink); }
  .intro-copy { font-weight: 400; fill: var(--ink); }
  .brand-name { font-weight: 600; fill: var(--blue-deep); }
  .brand-name-light { font-weight: 600; fill: var(--paper); }
  .brand-tagline { font-weight: 400; fill: var(--pink); }
  .brand-tagline-light { font-weight: 400; fill: var(--paper); }
  .web-address { font-weight: 400; fill: var(--paper); letter-spacing: 3px; }
  .contact-phone { font-weight: 700; fill: var(--paper); }
  .contact-line { font-weight: 400; fill: var(--paper); }
  .compliance-bold { font-weight: 700; fill: var(--paper); }
  .compliance-light { font-weight: 300; fill: var(--paper); }
</style>
</head>
<body>
<main class="canvas">
  <svg class="folder-dieline" viewBox="0 0 1163 1165" xmlns="http://www.w3.org/2000/svg">
    <defs>
      <linearGradient id="paperFade" x1="0" y1="0" x2="0" y2="1">
        <stop offset="0" stop-color="var(--paper-top)"/>
        <stop offset="1" stop-color="var(--paper-bottom)"/>
      </linearGradient>
      <linearGradient id="patternFade" x1="0" y1="0" x2="0" y2="1">
        <stop offset="0" stop-color="var(--pattern-grey)" stop-opacity="0"/>
        <stop offset="0.35" stop-color="var(--pattern-grey)" stop-opacity="0.75"/>
        <stop offset="1" stop-color="var(--pattern-grey)" stop-opacity="0.95"/>
      </linearGradient>
      <radialGradient id="labPhoto" cx="0.45" cy="0.42" r="0.65">
        <stop offset="0" stop-color="#e7b3b3"/>
        <stop offset="0.25" stop-color="#a9877f"/>
        <stop offset="0.55" stop-color="#5d7c8f"/>
        <stop offset="1" stop-color="#2c4a5d"/>
      </radialGradient>
      <clipPath id="folderShape">
        <path d="M0,0 H1163 V1162 H665 Q630,1162 625,1125 L583,917 L555,1125 Q548,1162 515,1162 H0 Z"/>
      </clipPath>
    </defs>

    <g clip-path="url(#folderShape)">
      <rect class="paper" x="0" y="0" width="1163" height="1165" fill="url(#paperFade)"/>

      <!-- faint watermark ring on back cover -->
      <circle class="back-watermark" cx="312" cy="122" r="92" fill="none" stroke="var(--watermark)" stroke-width="18"/>

      <!-- decorative molecular pattern area -->
      <rect class="molecule-pattern" role="img" aria-label="Faint grey hexagon molecule pattern with small medical icons" x="0" y="220" width="1163" height="360" fill="url(#patternFade)"/>

      <!-- wave bands -->
      <path class="wave-pink" d="M0,548 C250,470 460,540 700,628 C900,695 1050,640 1163,572 V1165 H0 Z" fill="var(--pink)"/>
      <path class="wave-blue" d="M0,562 C250,486 460,556 700,644 C900,711 1050,656 1163,588 V1165 H0 Z" fill="var(--blue)"/>

      <!-- hero circle -->
      <circle cx="885" cy="520" r="242" fill="var(--blue)"/>
      <circle cx="862" cy="525" r="228" fill="var(--paper)"/>
      <circle cx="843" cy="526" r="207" fill="var(--pink)"/>
      <circle role="img" aria-label="Photo: gloved hands holding a petri dish under glowing science icons" cx="853" cy="530" r="196" fill="url(#labPhoto)"/>

      <!-- brand lockup top right -->
      <circle cx="750" cy="68" r="30" fill="none" stroke="var(--blue-deep)" stroke-width="6"/>
      <text class="brand-name" x="795" y="78" font-size="38">Veridian Medical</text>
      <text class="brand-tagline" x="797" y="102" font-size="12">One step closer to healthier living</text>

      <!-- headline -->
      <text class="headline-light" x="854" y="174" font-size="47" text-anchor="middle">ONE STEP CLOSER</text>
      <text class="headline-bold" x="862" y="218" font-size="49" text-anchor="middle">TO HEALTHIER LIVING</text>
      <line x1="615" y1="229" x2="1115" y2="229" stroke="var(--blue)" stroke-width="2"/>
      <text class="intro-copy" x="862" y="257" font-size="20" text-anchor="middle">We've provided a variety of products at a</text>
      <text class="intro-copy" x="862" y="279" font-size="20" text-anchor="middle">national level for 20 years</text>

      <!-- front web address -->
      <text class="web-address" x="873" y="824" font-size="22" text-anchor="middle">www.veridianmedsupply.com</text>

      <!-- back cover contact block -->
      <circle cx="66" cy="668" r="22" fill="none" stroke="var(--paper)" stroke-width="4"/>
      <text class="brand-name-light" x="100" y="678" font-size="27">Veridian Medical</text>
      <text class="brand-tagline-light" x="102" y="696" font-size="9">One step closer to healthier living</text>

      <g class="contact-icons" fill="var(--paper)" stroke="var(--pink)" stroke-width="2">
        <circle cx="68" cy="728" r="9"/>
        <circle cx="68" cy="758" r="9"/>
        <circle cx="68" cy="789" r="9"/>
        <circle cx="68" cy="815" r="9"/>
      </g>
      <g class="contact-glyphs" fill="none" stroke="var(--ink)" stroke-width="1.6">
        <path d="M64,724 q0,8 8,8 l1,-3 -3,-2 -2,2 q-3,-1 -4,-4 l2,-2 -2,-3 z"/>
        <path d="M68,763 c-4,-5 -5,-7 -5,-9 a5,5 0 0 1 10,0 c0,2 -1,4 -5,9 z"/>
        <rect x="63" y="785" width="10" height="7"/>
        <path d="M63,785 l5,4 5,-4"/>
        <circle cx="68" cy="815" r="5"/>
        <path d="M63,815 h10 M68,810 v10"/>
      </g>
      <text class="contact-phone" x="92" y="734" font-size="21">555.014.2290</text>
      <text class="contact-line" x="92" y="757" font-size="13">2450 Harbor View Blvd Ste 120</text>
      <text class="contact-line" x="92" y="773" font-size="13">Coral Bay, FL 33000</text>
      <text class="contact-line" x="92" y="794" font-size="13">info@veridianmedsupply.com</text>
      <text class="contact-line" x="92" y="819" font-size="13">www.veridianmedsupply.com</text>

      <!-- accreditation badge and compliance -->
      <rect class="accreditation-badge" x="426" y="652" width="74" height="74" fill="var(--badge)" stroke="var(--paper)" stroke-width="3"/>
      <text class="compliance-bold" x="462" y="798" font-size="24" text-anchor="middle">HIPAA</text>
      <text class="compliance-light" x="462" y="826" font-size="24" text-anchor="middle">COMPLIANT</text>

      <!-- business card slot on left pocket -->
      <path class="card-slot" d="M189,925 H414 L449,960 V1067 L414,1102 H189 L154,1067 V960 Z" fill="var(--paper)"/>

      <!-- right pocket, printed upside down -->
      <g class="pocket-brand" transform="rotate(180 870 990)">
        <circle cx="780" cy="1006" r="26" fill="none" stroke="var(--paper)" stroke-width="5"/>
        <text class="brand-name-light" x="820" y="1014" font-size="32">Veridian Medical</text>
        <text class="brand-tagline-light" x="822" y="1032" font-size="10">One step closer to healthier living</text>
        <text class="contact-line" x="755" y="1060" font-size="13">www.veridianmedsupply.com</text>
      </g>
    </g>
  </svg>
</main>
</body>
</html>
```